HEARTHMILE business card and stationary design

We are looking for a simple yet elegant design for our mortgage company business card and stationary.

The card should include:
Name (Marcus Pell)
Title (CEO)
Phone Number (732-555-0182)
Address (48 Birchwell Court, Suite 314, Fernvale, NJ 07915)
Email (email@hearthmile.example)
"NMLS" i.e. (NMLS 61947)
"Company NMLS" (Company NMLS 274615)

Contact Information for Business Card

See above

```html
<!DOCTYPE html>
<html lang="en">
<head>
<meta charset="utf-8">
<title>Hearthmile Business Card</title>
<link href="https://fonts.googleapis.com/css2?family=Jost:wght@400;500;600&display=swap" rel="stylesheet">
<style>
  :root {
    --backdrop: #8e8e8e;
    --navy: #131f2a;
    --navy-soft: #1a2a38;
    --paper: #e1e2e4;
    --blue: #1592d6;
    --ink: #1b2630;
    --light-text: #dfe3e7;
  }
  * { margin: 0; padding: 0; box-sizing: border-box; }
  html, body {
    width: 1200px; height: 781px; overflow: hidden;
    background: var(--backdrop);
    font-family: "Jost", sans-serif;
  }
  .canvas { position: relative; width: 1200px; height: 781px; }
  .card {
    position: absolute; left: 358px; width: 452px; height: 251px; overflow: hidden;
  }
  .card-front {
    top: 103px;
    background: radial-gradient(ellipse at 50% 100%, var(--navy-soft), var(--navy) 70%);
    display: flex; align-items: center; justify-content: center;
  }
  .front-wordmark {
    font-size: 40px; font-weight: 500; color: var(--light-text); letter-spacing: 6px;
    text-transform: uppercase;
  }
  .card-back { top: 408px; }
  .back-top { position: absolute; inset: 0 0 99px 0; background: var(--paper); }
  .back-bottom { position: absolute; left: 0; right: 0; bottom: 0; height: 99px; background: var(--navy); }
  .back-wordmark {
    position: absolute; left: 28px; top: 38px;
    font-size: 24px; font-weight: 500; color: var(--ink); line-height: 1;
    letter-spacing: 4px; text-transform: uppercase;
  }
  .holder { position: absolute; left: 28px; top: 109px; }
  .holder-name {
    font-size: 15.5px; font-weight: 600; letter-spacing: 1.4px; color: var(--blue);
    text-transform: uppercase; line-height: 1.1;
  }
  .holder-title { font-size: 13px; color: var(--ink); line-height: 1.3; }
  .name-rule {
    position: absolute; left: 28px; top: 150px; width: 120px; height: 3px; background: var(--blue);
  }
  .contact { position: absolute; left: 28px; color: var(--light-text); font-size: 12.5px; line-height: 1; display: flex; align-items: center; gap: 6px; }
  .contact svg { width: 12px; height: 12px; }
  .contact-phone { top: 170px; }
  .contact-email { top: 189px; }
  .contact-address { top: 219px; }
  .licences {
    position: absolute; right: 27px; top: 203px; text-align: right;
    color: var(--light-text); font-size: 11px; line-height: 15px;
  }
</style>
</head>
<body>
<div class="canvas">
  <section class="card card-front">
    <span class="front-wordmark">Hearthmile</span>
  </section>

  <section class="card card-back">
    <div class="back-top"></div>
    <div class="back-bottom"></div>
    <span class="back-wordmark">Hearthmile</span>
    <div class="holder">
      <p class="holder-name">Marcus Pell</p>
      <p class="holder-title">CEO</p>
    </div>
    <div class="name-rule"></div>

    <p class="contact contact-phone">
      <svg viewBox="0 0 24 24" fill="none" stroke="#1592d6" stroke-width="2"><path d="M5 3h4l2 5-3 2a12 12 0 0 0 6 6l2-3 5 2v4a2 2 0 0 1-2 2A18 18 0 0 1 3 5a2 2 0 0 1 2-2z"/></svg>
      732-555-0182
    </p>
    <p class="contact contact-email">
      <svg viewBox="0 0 24 24" fill="none" stroke="#1592d6" stroke-width="2"><rect x="2" y="5" width="20" height="14"/><path d="M2 5l10 8 10-8"/></svg>
      email@hearthmile.example
    </p>
    <p class="contact contact-address">48 Birchwell Court, Suite 314, Fernvale, NJ 07915</p>

    <div class="licences">
      <p>NMLS 61947</p>
      <p>Company NMLS 274615</p>
    </div>
  </section>
</div>
</body>
</html>
```